Website redesign - vorelmik.com

We are looking to do a full redesign of vorelmik.com. Need a designer to come up overall layout and 3 specific pages and 3 different hero images.
Wireframes for the 3 pages are attached as well as site images. You don't have to follow the wireframes exactly, but instead the wireframe is there to show you the information that needs to be on each page. Feel free to rearrange as needed.
Our target market is self taught engineers. So definitely I want a more casual feel to it. I'm ok with fun bold colors as well. Really like websites that have the infinite scroll look/feel to them.
Looking to find a designer who will produce HTML and potentially even implement the HTML into our site checked in code.
HTML Code should be responsive/mobile first leveraging Bootstrap 4.
Attached files include:
0) Wireframe PDF
https://files.plomwerk.net/d/7Kx2pQmW9zLr4TbN8vYc3HsE5fJ/view?mode=share
1) Vorelmik Images zip 1
https://files.plomwerk.net/d/4Gt8nRvB2wQx6MkZ1pLd9YaC7hU/view?mode=share
2) Vorelmik Images zip 2
https://files.plomwerk.net/d/9Jw3sTcF5yNv1HqX8rKb2ZeM6dP/view?mode=share
Target Market(s)
I sell DIY Waterproof Electronics enclosures. Target audience is self taught DIY engineers
Coding
Coded - Design and coding required
Number of Pages Required
3 page
Colors
Designer to choose colors to be used in the design.
Look and feel

```html
<!DOCTYPE html>
<html lang="en">
<head>
<meta charset="utf-8">
<title>Vorelmik — Designs</title>
<link rel="stylesheet" href="https://fonts.googleapis.com/css2?family=Michroma&family=Poppins:wght@400;500;600&display=swap">
<style>
:root{
  --brand-blue:#0000f5;
  --accent-yellow:#cfd600;
  --ink:#1d1d1d;
  --muted:#6b6b6b;
  --card-bg:#f4f4f4;
  --rule:#e4e4e4;
  --white:#ffffff;
}
*{margin:0;padding:0;box-sizing:border-box}
html,body{width:1200px;height:2556px;overflow:hidden;background:var(--white);font-family:'Poppins',sans-serif;color:var(--ink)}
.page{position:relative;width:1200px;height:2556px}
.site-header{position:absolute;top:0;left:0;width:1200px;height:89px;background:var(--white);box-shadow:0 4px 10px rgba(0,0,0,.07);z-index:2}
.brand{position:absolute;left:89px;top:18px;display:flex;align-items:center;gap:8px;color:var(--brand-blue);font-family:'Poppins',sans-serif;font-weight:600;font-size:40px;line-height:1;letter-spacing:-.5px}
.brand-dot{width:14px;height:14px;border-radius:50%;background:var(--accent-yellow)}
.main-nav{position:absolute;left:348px;top:36px;display:flex;gap:40px;font-size:13px;font-weight:500;letter-spacing:.2px}
.main-nav a{color:var(--ink);text-decoration:none}
.auth-btn{position:absolute;left:950px;top:21px;width:169px;height:48px;background:var(--accent-yellow);border-radius:4px;color:var(--white);font-size:12px;font-weight:600;display:flex;align-items:center;justify-content:center;gap:6px}
.catalog-section{position:absolute;left:89px;width:1030px}
.section-title{font-family:'Michroma',sans-serif;font-size:24px;letter-spacing:.5px;color:var(--ink);height:50px;line-height:30px}
.card-row{display:flex;gap:7px}
.product-card{width:201px;height:372px;background:var(--card-bg);padding:0 20px}
.product-photo{display:block;width:160px;height:130px;margin:25px auto 0;border-radius:4px}
.spec-block{margin-top:0}
.spec-block h3{font-size:15.5px;font-weight:500;line-height:20px}
.spec-block p{font-size:10.5px;color:var(--muted);line-height:16px}
.spec-power{margin-top:21px}
.spec-space{margin-top:11px}
.spec-size{margin-top:12px}
.section-rule{position:absolute;left:89px;width:1030px;height:1px;background:var(--rule)}
.site-footer{position:absolute;left:0;top:2367px;width:1200px;height:189px;background:var(--brand-blue);color:var(--white)}
.footer-brand{position:absolute;left:89px;top:48px;display:flex;align-items:center;gap:8px;font-size:48px;font-weight:600;line-height:1}
.social-links{position:absolute;right:81px;top:51px;display:flex;gap:36px}
.social-link{display:flex;align-items:center;gap:8px;font-size:14px;font-weight:500}
.social-circle{width:43px;height:43px;border-radius:50%;background:rgba(255,255,255,.18)}
.footer-rule{position:absolute;left:89px;top:145px;width:1030px;height:1px;background:rgba(255,255,255,.35)}
.copyright{position:absolute;left:0;top:167px;width:1200px;text-align:center;font-size:13px;font-weight:500}
.back-to-top{position:absolute;left:1132px;top:2491px;width:50px;height:50px;border-radius:50%;background:var(--accent-yellow);display:flex;align-items:center;justify-content:center}
</style>
</head>
<body>
<div class="page">
  <header class="site-header">
    <div class="brand"><span class="brand-dot"></span>Vorelmik</div>
    <nav class="main-nav">
      <a href="#">GET STARTED</a><a href="#">DESIGNS</a><a href="#">FAQS</a><a href="#">VIDEOS</a><a href="#">CONTACT US</a>
    </nav>
    <div class="auth-btn">
      <svg width="14" height="14" viewBox="0 0 14 14" fill="none" stroke="#fff" stroke-width="1.3"><path d="M7 1h5v12H7M1 7h8M6 4l3 3-3 3"/></svg>
      SIGN IN / SIGN UP
    </div>
  </header>

  <section class="catalog-section" style="top:175px">
    <h2 class="section-title">VORELMIK PREMIUM GROVEBOX ENCLOSURES</h2>
    <div class="card-row">
      <article class="product-card"><div class="product-photo" role="img" aria-label="Open white enclosure with black circuit boards" style="background:linear-gradient(160deg,#e8e8e8,#2a2a2a)"></div><div class="spec-block spec-power"><h3>Power Options</h3><p>4x - Brightcell 350w</p><p>2x - KX Common Slot - 1200w</p></div><div class="spec-block spec-space"><h3>Component Space</h3><p>Double Decker</p><p>127sq real estate</p></div><div class="spec-block spec-size"><h3>Enclosure Size</h3><p>27in x 14in x 7in (height)</p></div></article>
      <article class="product-card"><div class="product-photo" role="img" aria-label="Enclosure panel with green relay boards" style="background:linear-gradient(160deg,#3a7a4a,#2b2b2b)"></div><div class="spec-block spec-power"><h3>Power Options</h3><p>4x - Brightcell 350w</p><p>2x - KX Common Slot - 1200w</p></div><div class="spec-block spec-space"><h3>Component Space</h3><p>Double Decker</p><p>127sq real estate</p></div><div class="spec-block spec-size"><h3>Enclosure Size</h3><p>27in x 14in x 7in (height)</p></div></article>
      <article class="product-card"><div class="product-photo" role="img" aria-label="Closed white enclosure beside a drink can" style="background:linear-gradient(160deg,#f7f7f4,#d9d9d4)"></div><div class="spec-block spec-power"><h3>Power Options</h3><p>4x - Brightcell 350w</p><p>2x - KX Common Slot - 1200w</p></div><div class="spec-block spec-space"><h3>Component Space</h3><p>Double Decker</p><p>127sq real estate</p></div><div class="spec-block spec-size"><h3>Enclosure Size</h3><p>27in x 14in x 7in (height)</p></div></article>
      <article class="product-card"><div class="product-photo" role="img" aria-label="Open enclosure with power supply units inside" style="background:linear-gradient(160deg,#e6e6e6,#8a8a7a)"></div><div class="spec-block spec-power"><h3>Power Options</h3><p>4x - Brightcell 350w</p><p>2x - KX Common Slot - 1200w</p></div><div class="spec-block spec-space"><h3>Component Space</h3><p>Double Decker</p><p>127sq real estate</p></div><div class="spec-block spec-size"><h3>Enclosure Size</h3><p>27in x 14in x 7in (height)</p></div></article>
      <article class="product-card"><div class="product-photo" role="img" aria-label="Wooden mounting plate kit with hardware bag" style="background:linear-gradient(160deg,#c9a06e,#9a7448)"></div><div class="spec-block spec-power"><h3>Power Options</h3><p>4x - Brightcell 350w</p><p>2x - KX Common Slot - 1200w</p></div><div class="spec-block spec-space"><h3>Component Space</h3><p>Double Decker</p><p>127sq real estate</p></div><div class="spec-block spec-size"><h3>Enclosure Size</h3><p>27in x 14in x 7in (height)</p></div></article>
    </div>
  </section>
  <div class="section-rule" style="top:669px"></div>

  <section class="catalog-section" style="top:735px">
    <h2 class="section-title">RKV AMMO CRATES</h2>
    <div class="card-row">
      <article class="product-card"><div class="product-photo" role="img" aria-label="Dark green ammo crate" style="background:linear-gradient(160deg,#2f5a3c,#16281b)"></div><div class="spec-block spec-power"><h3>Power Options</h3><p>4x - Brightcell 350w</p><p>2x - KX Common Slot - 1200w</p></div><div class="spec-block spec-space"><h3>Component Space</h3><p>Double Decker</p><p>127sq real estate</p></div><div class="spec-block spec-size"><h3>Enclosure Size</h3><p>27in x 14in x 7in (height)</p></div></article>
      <article class="product-card"><div class="product-photo" role="img" aria-label="Olive ammo crate" style="background:linear-gradient(160deg,#7c7d56,#55563a)"></div><div class="spec-block spec-power"><h3>Power Options</h3><p>4x - Brightcell 350w</p><p>2x - KX Common Slot - 1200w</p></div><div class="spec-block spec-space"><h3>Component Space</h3><p>Double Decker</p><p>127sq real estate</p></div><div class="spec-block spec-size"><h3>Enclosure Size</h3><p>27in x 14in x 7in (height)</p></div></article>
      <article class="product-card"><div class="product-photo" role="img" aria-label="Translucent lavender crate" style="background:linear-gradient(160deg,#e4e0fb,#b8b0ee)"></div><div class="spec-block spec-power"><h3>Power Options</h3><p>4x - Brightcell 350w</p><p>2x - KX Common Slot - 1200w</p></div><div class="spec-block spec-space"><h3>Component Space</h3><p>Double Decker</p><p>127sq real estate</p></div><div class="spec-block spec-size"><h3>Enclosure Size</h3><p>27in x 14in x 7in (height)</p></div></article>
    </div>
  </section>
  <div class="section-rule" style="top:1229px"></div>

  <section class="catalog-section" style="top:1295px">
    <h2 class="section-title">CABLE GUARD (CG) ENCLOSURES</h2>
    <div class="card-row">
      <article class="product-card"><div class="product-photo" role="img" aria-label="Power supplies mounted on a black panel" style="background:linear-gradient(160deg,#cfcfcf,#2a2a2a)"></div><div class="spec-block spec-power"><h3>Power Options</h3><p>4x - Brightcell 350w</p><p>2x - KX Common Slot - 1200w</p></div><div class="spec-block spec-space"><h3>Component Space</h3><p>Double Decker</p><p>127sq real estate</p></div><div class="spec-block spec-size"><h3>Enclosure Size</h3><p>27in x 14in x 7in (height)</p></div></article>
      <article class="product-card"><div class="product-photo" role="img" aria-label="Wooden plate with hardware bag" style="background:linear-gradient(160deg,#caa06a,#9c7442)"></div><div class="spec-block spec-power"><h3>Power Options</h3><p>4x - Brightcell 350w</p><p>2x - KX Common Slot - 1200w</p></div><div class="spec-block spec-space"><h3>Component Space</h3><p>Double Decker</p><p>127sq real estate</p></div><div class="spec-block spec-size"><h3>Enclosure Size</h3><p>27in x 14in x 7in (height)</p></div></article>
    </div>
  </section>
  <div class="section-rule" style="top:1788px"></div>

  <section class="catalog-section" style="top:1855px">
    <h2 class="section-title">SPECIALTY ENCLOSURES</h2>
    <div class="card-row">
      <article class="product-card"><div class="product-photo" role="img" aria-label="Aluminium tube enclosure with black cables" style="background:linear-gradient(160deg,#e2e2e2,#1f1f1f)"></div><div class="spec-block spec-power"><h3>Power Options</h3><p>4x - Brightcell 350w</p><p>2x - KX Common Slot - 1200w</p></div><div class="spec-block spec-space"><h3>Component Space</h3><p>Double Decker</p><p>127sq real estate</p></div><div class="spec-block spec-size"><h3>Enclosure Size</h3><p>27in x 14in x 7in (height)</p></div></article>
    </div>
  </section>

  <footer class="site-footer">
    <div class="footer-brand"><span class="brand-dot"></span>Vorelmik</div>
    <div class="social-links">
      <div class="social-link"><span class="social-circle"></span>FEEDLINE</div>
      <div class="social-link"><span class="social-circle"></span>SNAPGRID</div>
    </div>
    <div class="footer-rule"></div>
    <p class="copyright">COPYRIGHT 2020 @ VORELMIK DESIGNER.</p>
  </footer>
  <div class="back-to-top">
    <svg width="14" height="18" viewBox="0 0 14 18" fill="none" stroke="#fff" stroke-width="1.4"><path d="M7 17V2M2 7l5-5 5 5"/></svg>
  </div>
</div>
</body>
</html>
```